Web Developer Needs a Business Card Design

I need a personal business card design that represents me as a web developer for potential employers. I would like the background to be a dark color on the front for contrast with my logo and name. The back will have all my information along with a smaller version of the logo. I want something with a modern look and feel, not too conservative. This will be used for potential employers and freelance work.

Industry/Entity Type

Business

Contact Information for Business Card

Front should have my logo and name. The back should have all my personal information which would include: name: Tom Varulek, phone: 570-614-3098, email: tomvarulek@quillbox.net, website url: www.tomvarulek.net, logo, web developer.

Font styles to use
Sans Serif

Requirements
Must have
• Must include my logo. The color palette base color will be the logo color.

```html
<!DOCTYPE html>
<html lang="en">
<head>
<meta charset="utf-8">
<title>Tom Varulek — Business Card</title>
<link rel="stylesheet" href="https://fonts.googleapis.com/css2?family=Open+Sans:wght@300;400;600;700&display=swap">
<style>
  :root {
    --teal: #5cbfa5;
    --teal-deep: #3fa88c;
    --ink: #0c0c0c;
    --paper: #ffffff;
    --text-dark: #1d1d1d;
    --stage: #e9e7e3;
  }
  * { box-sizing: border-box; margin: 0; padding: 0; }
  html, body {
    width: 1200px; height: 913px; overflow: hidden;
    background: var(--stage);
    font-family: "Open Sans", Arial, sans-serif;
  }
  .stage { position: relative; width: 1200px; height: 913px; }

  .card {
    position: absolute; top: 306px;
    width: 520px; height: 300px;
    border-radius: 16px; overflow: hidden;
    background: var(--paper);
    box-shadow: 0 2px 6px rgba(0,0,0,.12);
  }
  .card--contact { left: 50px; background: var(--ink); }
  .card--identity { left: 630px; }

  .card__shape { position: absolute; inset: 0; }

  .brand {
    position: absolute; display: flex; align-items: center; justify-content: center;
    border: 12px solid var(--teal); border-radius: 50%;
    color: var(--teal); font-weight: 600; text-align: center; line-height: 1.1;
  }
  .card--contact .brand { left: 40px; top: 70px; width: 170px; height: 170px; font-size: 22px; }
  .card--identity .brand { left: 212px; top: 40px; width: 96px; height: 96px; border-width: 7px; font-size: 14px; }

  .contact {
    position: absolute; right: 28px; top: 34px; text-align: right; color: var(--paper);
  }
  .contact__name { font-size: 22px; font-weight: 700; letter-spacing: .5px; line-height: 1.1; }
  .contact__role { font-size: 12px; font-weight: 700; color: var(--teal); letter-spacing: .8px; margin-bottom: 12px; }
  .contact__line { display: flex; justify-content: flex-end; align-items: center; gap: 7px; font-size: 13px; line-height: 21px; white-space: nowrap; }
  .contact__icon { width: 12px; height: 12px; flex: none; }

  .identity { position: absolute; left: 0; right: 0; top: 160px; text-align: center; color: var(--text-dark); }
  .identity__name { font-size: 36px; font-weight: 300; letter-spacing: 2px; }
  .identity__role { font-size: 15px; font-weight: 400; margin-top: 6px; }
</style>
</head>
<body>
<main class="stage">

  <section class="card card--contact">
    <svg class="card__shape" viewBox="0 0 520 300" width="520" height="300" aria-hidden="true">
      <path d="M0 0 H162 Q302 110 342 300 H0 Z" fill="var(--teal)"/>
      <path d="M0 0 H150 Q290 110 330 300 H0 Z" fill="var(--paper)"/>
    </svg>
    <div class="brand">Tom<br>Varulek</div>
    <div class="contact">
      <p class="contact__name">TOM VARULEK</p>
      <p class="contact__role">WEB DEVELOPER</p>
      <p class="contact__line">570-614-3098
        <svg class="contact__icon" viewBox="0 0 24 24"><path fill="var(--teal)" d="M6.6 10.8a15 15 0 0 0 6.6 6.6l2.2-2.2c.3-.3.7-.4 1-.2 1.1.4 2.3.6 3.6.6.6 0 1 .4 1 1V20c0 .6-.4 1-1 1A17 17 0 0 1 3 4c0-.6.4-1 1-1h3.5c.6 0 1 .4 1 1 0 1.3.2 2.5.6 3.6.1.3 0 .7-.2 1z"/></svg>
      </p>
      <p class="contact__line">tomvarulek@quillbox.net
        <svg class="contact__icon" viewBox="0 0 24 24"><rect x="2" y="5" width="20" height="14" rx="1.5" fill="none" stroke="var(--teal)" stroke-width="2.4"/><path d="M3 6l9 7 9-7" fill="none" stroke="var(--teal)" stroke-width="2.4"/></svg>
      </p>
      <p class="contact__line">www.tomvarulek.net
        <svg class="contact__icon" viewBox="0 0 24 24"><circle cx="12" cy="12" r="10" fill="none" stroke="var(--teal)" stroke-width="2.4"/><path d="M2 12h20M12 2c3 3 3 17 0 20M12 2c-3 3-3 17 0 20" fill="none" stroke="var(--teal)" stroke-width="2"/></svg>
      </p>
    </div>
  </section>

  <section class="card card--identity">
    <div class="brand">Tom<br>Varulek</div>
    <div class="identity">
      <h1 class="identity__name">TOM VARULEK</h1>
      <p class="identity__role">Front-End Developer</p>
    </div>
  </section>

</main>
</body>
</html>
```